Business Card - high end, modern health care

Hey designers!

We need a double sided business card for the boutique, cutting edge physical therapy rehabilitation centre in Sydney's Northern Beaches.

With the most qualified physios in the area The Harbourview Motion Clinic does what other physiotherapy practices do not, we take our time with our patients giving them longer appointments, better physios and therefor faster results!

We guarantee that the service people receive at THMC will be unparalleled.

Hence we need a business card to reflect our modern, boutique, high end service. The final design needs to reflect that we are in a class of our own yet with the feel of beachside retreat.

Below I have attached our logo in both blue on white and white on blue. The exact colour is;
and the font that we have used in our logo is Tex Gyre Aventador.

I like the idea of the blue as the main colour as it is more eye catching and our signage onto the main road will be in this blue and in the interest of consistency across marketing the blue needs to be a part of the design. However I would appreciate a few designs onto a wooden background as this is a visual theme within the fitout of the practice.

The design needs to be of standard size (91x55mm).

Target Market(s)

We target people who have an end outcome in mind and those who have had poor experiences with other providers and ensure that everyone gets the care that they deserve with a premium service that is tailored to the individuals circumstances. As a premium service, the target market is highly educated, business and tech savvy with the additional target market of elderly people who have self funded their retirement and see value in paying for the best ongoing rehabilitation to maintain independence.

Industry/Entity Type

Physical Therapy

Contact Information for Business Card

Name, designation( Titled Musculoskeletal Physiotherapist... there will also be those in the company that have multiple designations ie 5 or 6 words long), phone number, email, facebook, instagram, address

Font styles to use
Sans Serif

Colors

Designer to choose colors to be used in the design.

Requirements
Must have
• Front - The logo as large as possible, blue or wooden theme, and all of the important details.
• Back - A blank space/lines on which to write appointment times (no "Appointment, date, time" etc.)
Nice to have
• facebook url
• logos for facebook and instagram
• Mini logos for the phone and email?

```html
<!DOCTYPE html>
<html lang="en">
<head>
<meta charset="utf-8">
<title>The Harbourview Motion Clinic — Business Card</title>
<link href="https://fonts.googleapis.com/css2?family=Raleway:wght@400;500;700&display=swap" rel="stylesheet">
<style>
  :root {
    --brand-blue: #0d55a6;
    --ink: #1b1b1b;
    --paper: #fafafa;
    --rule: #222222;
    --dash: #9a9a9a;
    --band-grey: #d3d4d6;
    --stage: #ecebe8;
  }
  * { box-sizing: border-box; margin: 0; padding: 0; }
  html, body { width: 1200px; height: 1200px; overflow: hidden; }
  body {
    background: var(--stage);
    font-family: "Raleway", sans-serif;
    color: var(--ink);
    display: flex;
    flex-direction: column;
    align-items: center;
    justify-content: center;
    gap: 60px;
  }
  .card {
    position: relative;
    width: 840px;
    height: 508px;
    overflow: hidden;
    box-shadow: 0 6px 18px rgba(0,0,0,0.12);
  }

  /* Front */
  .card--front {
    background: var(--brand-blue);
    display: flex;
    align-items: center;
    justify-content: center;
  }
  .brand {
    display: flex;
    align-items: center;
    gap: 22px;
    font-weight: 700;
  }
  .brand__dot {
    width: 84px; height: 84px;
    border-radius: 50%;
    background: currentColor;
    flex: none;
  }
  .brand__name {
    font-size: 40px;
    line-height: 1.1;
    letter-spacing: 1px;
    text-transform: uppercase;
  }
  .card--front .brand { color: #ffffff; }

  /* Back */
  .card--back { background: var(--paper); }
  .person {
    position: absolute; left: 56px; top: 62px;
  }
  .person__name { font-size: 36px; font-weight: 400; }
  .person__name em { font-style: normal; color: var(--brand-blue); }
  .person__role { font-size: 15px; margin-top: 4px; }

  .rule {
    position: absolute; height: 1.5px; background: var(--rule);
  }
  .rule--top { left: 50px; right: 50px; top: 152px; }
  .rule--mid { left: 50px; right: 50px; top: 268px; }
  .rule--write {
    left: 50px; right: 50px; top: 392px; height: 0;
    background: none; border-top: 1.5px dashed var(--dash);
  }

  .contact {
    position: absolute; left: 56px; top: 176px;
    list-style: none; font-size: 21px;
  }
  .contact li { display: flex; align-items: center; gap: 16px; height: 40px; }
  .contact svg { width: 24px; height: 24px; flex: none; }

  .card--back .brand {
    position: absolute; right: 50px; top: 62px;
    color: var(--brand-blue); gap: 12px;
  }
  .card--back .brand__dot { width: 40px; height: 40px; }
  .card--back .brand__name { font-size: 20px; }

  .social {
    position: absolute; right: 50px; top: 160px;
    list-style: none; font-size: 19px;
  }
  .social li { display: flex; align-items: center; gap: 12px; height: 40px; }
  .social__dot { width: 22px; height: 22px; border-radius: 50%; background: var(--brand-blue); flex: none; }

  .band {
    position: absolute; left: 0; right: 0; bottom: 0; height: 46px;
  }
  .band__grey { position: absolute; left: 0; top: 22px; bottom: 0; width: 360px; background: var(--band-grey); }
  .band__blue {
    position: absolute; left: 340px; right: 0; top: 0; bottom: 0;
    background: var(--brand-blue); border-top-left-radius: 40px;
  }
</style>
</head>
<body>

<section class="card card--front" aria-label="Card front">
  <div class="brand">
    <span class="brand__dot"></span>
    <span class="brand__name">The Harbourview<br>Motion Clinic</span>
  </div>
</section>

<section class="card card--back" aria-label="Card back">
  <div class="person">
    <p class="person__name">Name of <em>Person</em></p>
    <p class="person__role">Designation</p>
  </div>

  <div class="brand">
    <span class="brand__dot"></span>
    <span class="brand__name">The Harbourview<br>Motion Clinic</span>
  </div>

  <div class="rule rule--top"></div>

  <ul class="contact">
    <li>
      <svg viewBox="0 0 24 24" aria-hidden="true"><circle cx="12" cy="12" r="10.5" fill="none" stroke="#1b1b1b" stroke-width="1.8"/><path d="M9 7.5c-1 .6-1.5 1.6-1.2 3 .6 2.4 2.4 4.6 4.8 5.7 1.3.5 2.4.2 3.1-.7l-1.7-1.6-1.2.7c-1-.5-2-1.6-2.4-2.6l.8-1.1z" fill="#1b1b1b"/></svg>
      <span>02 9481 5520</span>
    </li>
    <li>
      <svg viewBox="0 0 24 24" aria-hidden="true"><rect x="2" y="5" width="20" height="14" fill="#1b1b1b"/><path d="M2 5l10 8 10-8" fill="none" stroke="#fafafa" stroke-width="1.4"/></svg>
      <span>hello@harbourviewmotion.com</span>
    </li>
  </ul>

  <ul class="social">
    <li><span class="social__dot"></span><span>social/name</span></li>
    <li><span class="social__dot"></span><span>profile_name</span></li>
  </ul>

  <div class="rule rule--mid"></div>

  <div class="rule rule--write"></div>

  <div class="band">
    <div class="band__grey"></div>
    <div class="band__blue"></div>
  </div>
</section>

</body>
</html>
```